UI Improvement for FlorKeep app

We are looking for a talented UI/UX designer to REFINE and enhance the visual design of our mobile application, FlorKeep. The app is fully functional, but we need a designer to improve its aesthetics by specifying design elements such as fonts, colors, spacing, and component styles.
Your task will be to analyze the CURRENT UI and provide detailed design specifications that will make the app more visually appealing, modern, and user-friendly.
TODO:
Review the existing FlorKeep app design (see attachments) and identify areas for visual improvement.
Provide a detailed UI style guide, including:
Typography (font choices, sizes, and weights)
Color palette (primary, secondary, and accent colors)
Component styling (buttons, forms, icons, and interactive elements)
Spacing and layout guidelines (margins, paddings, and alignment)
Ensure the design remains clean, modern, and professional while maintaining usability and accessibility.
Provide design mockups or visual examples (if possible) to illustrate the proposed changes.
Deliverables:
A UI Style Guide (PDF or Figma file) with specifications on fonts, colors, spacing, and UI components.
Optionally, before/after mockups or examples demonstrating the improvements.
Ideal Designer:
Strong experience in mobile UI/UX design.
Understanding of modern design trends and best practices.
Ability to communicate design choices clearly for easy developer implementation.
I have attached 7 images showcasing the main UI screens used in the FlorKeep app. These screens need visual enhancements to improve their overall look and user experience.
The images represent the current design in three key modes:
LIST Mode – Displays data in a structured list format.
READ Mode – Shows detailed information when a user selects an item.
ADD/EDIT Mode – Allows users to input or modify information.
Additionally, there is a ‘MORE’ page, which serves as a menu listing other features of the application.
Task Objective:
Please refine and improve these UIs to create a more modern, visually appealing, and user-friendly experience. Focus on typography, colors, spacing, and component styling to ensure a cohesive and polished design.
Look and feel
Each slider illustrates characteristics of the customer's brand and the style your logo design should communicate.

```html
<!DOCTYPE html>
<html lang="en">
<head>
<meta charset="utf-8">
<title>FlorKeep – App Screens</title>
<link href="https://fonts.googleapis.com/css2?family=Roboto:wght@400;500;700&display=swap" rel="stylesheet">
<style>
:root{
  --bg-top:#02a98e;
  --bg-bottom:#0a55b0;
  --brand-blue:#0a4fb0;
  --brand-teal:#06a98a;
  --surface:#f1f1f3;
  --card:#f7f7f8;
  --field:#ffffff;
  --line:#e2e3e6;
  --text:#2b2b2b;
  --muted:#4a4a4a;
  --label-teal:#0aa37f;
  --white:#ffffff;
}
*{box-sizing:border-box;margin:0;padding:0}
html,body{width:1200px;height:583px;overflow:hidden}
body{
  font-family:"Roboto",sans-serif;
  background:linear-gradient(180deg,var(--bg-top) 0%,#049a9c 40%,var(--bg-bottom) 100%);
  position:relative;color:var(--text);
}
.screen{
  position:absolute;top:77px;width:198px;height:428px;
  background:var(--surface);border-radius:14px;overflow:hidden;
  box-shadow:0 4px 16px rgba(0,0,0,.18);
}
.screen--contact-edit{left:69px}
.screen--pilots{left:357px}
.screen--contact-read{left:645px}
.screen--work-order{left:933px}

.appbar{position:absolute;left:0;top:0;width:100%;height:56px;background:var(--brand-blue);color:var(--white)}
.status{position:absolute;top:5px;left:11px;right:11px;display:flex;justify-content:space-between;align-items:center;font-size:7px;font-weight:700}
.status svg{width:22px;height:7px}
.appbar__title{position:absolute;top:27px;left:0;width:100%;text-align:center;font-size:12px;font-weight:700}
.back{position:absolute;left:13px;top:26px;width:17px;height:17px;border-radius:50%;background:var(--brand-teal);display:flex;align-items:center;justify-content:center}
.back svg{width:7px;height:7px}
.action-plus{position:absolute;right:12px;top:26px;font-size:12px;font-weight:400;line-height:17px}
.btn-save{position:absolute;right:12px;top:27px;background:var(--brand-blue);border:1px solid #1e63c6;border-radius:3px;font-size:7px;font-weight:700;padding:4px 7px;box-shadow:0 1px 3px rgba(0,0,0,.25)}

.content{position:absolute;top:56px;left:0;right:0;bottom:30px;overflow:hidden}
.tabbar{position:absolute;bottom:0;left:0;width:100%;height:30px;background:var(--brand-teal);display:flex;justify-content:space-around;align-items:center;padding:0 6px}
.tab{width:16px;height:16px;display:flex;align-items:center;justify-content:center;border-radius:50%}
.tab svg{width:11px;height:11px;fill:var(--white)}
.tab--active{background:var(--white)}
.tab--active svg{fill:var(--brand-blue)}

.card{background:var(--card);border-radius:6px;box-shadow:0 0 3px rgba(0,0,0,.06)}
.form-card{position:absolute;left:13px;right:12px;padding:9px 9px 10px}
.field-label{font-size:6px;color:var(--muted);margin-bottom:4px}
.field{height:21px;background:var(--field);border-radius:3px;box-shadow:0 1px 2px rgba(0,0,0,.08);margin-bottom:8px}
.row3{display:flex;gap:4px}
.row3>div{flex:1}

.search-label{position:absolute;left:21px;top:10px;font-size:6px}
.search{position:absolute;left:21px;top:19px;width:154px;height:21px;background:var(--field);border-radius:3px;box-shadow:0 1px 2px rgba(0,0,0,.08)}
.search__btn{position:absolute;right:2px;top:2px;width:16px;height:17px;border-radius:2px;background:var(--brand-blue);display:flex;align-items:center;justify-content:center}
.search__btn svg{width:7px;height:7px}
.pilot-list{position:absolute;left:13px;right:12px;top:47px;height:280px;padding:10px 10px}
.pilot{display:flex;align-items:center;height:38px}
.avatar{width:27px;height:27px;border-radius:50%;border:1.5px solid var(--white);box-shadow:0 0 0 1px #c9ccd2;color:var(--white);font-weight:700;font-size:10px;display:flex;align-items:center;justify-content:center;flex:none}
.pilot__body{margin-left:4px}
.pilot__name{font-size:7.5px;color:var(--text)}
.pilot__date{display:inline-block;margin-top:2px;font-size:6px;padding:1px 5px;border:1px solid #cfd1d6;border-radius:6px;background:var(--white)}

.add-group{position:absolute;left:13px;right:12px;top:10px;padding:8px 9px}
.add-row{display:flex;align-items:center;height:22px;background:var(--white);border-radius:3px;box-shadow:0 1px 2px rgba(0,0,0,.07);padding-left:6px;font-size:6px;margin-bottom:4.5px}
.plus-dot{width:11px;height:11px;border-radius:50%;background:var(--brand-blue);color:var(--white);font-size:8px;line-height:11px;text-align:center;margin-right:5px;flex:none}
.linked-group{position:absolute;left:13px;right:12px;top:208px;height:140px;padding:7px 10px}
.linked{border-radius:2px;padding:8px 9px 9px;color:var(--white);margin-bottom:6px}
.linked--teal{background:var(--brand-teal)}
.linked--blue{background:var(--brand-blue)}
.linked__head{display:flex;justify-content:space-between;font-size:6px;margin-bottom:6px}
.linked__head b{font-weight:700}
.select{background:var(--white);color:#555;border-radius:2px;font-size:5px;line-height:1.5;padding:4px 18px 4px 4px;position:relative}
.select__caret{position:absolute;right:3px;top:3px;width:10px;height:10px;border-radius:50%;background:#e6e7ea;display:flex;align-items:center;justify-content:center}
.select__caret svg{width:5px;height:3px}

.chips{position:absolute;left:11px;top:10px;display:flex;gap:3px;align-items:center}
.chip{font-size:5px;padding:3px 6px;border:1px solid #c9ccd2;border-radius:7px;background:var(--white);color:#333}
.chip--active{border-color:var(--brand-teal);color:var(--label-teal);background:#e9f7f3}
.chip-tools{position:absolute;right:17px;top:12px;display:flex;gap:6px}
.chip-tools svg{width:7px;height:7px;fill:var(--brand-blue)}
.wo-group{position:absolute;left:13px;right:12px;top:34px;height:270px;padding:10px 9px}
.wo-detail{background:var(--white);border-radius:3px;padding:4px 8px 0}
.wo-field{border-bottom:1px solid var(--line);padding:5px 0 4px;position:relative}
.wo-field:last-child{border-bottom:none}
.wo-field__label{font-size:5px;color:var(--label-teal)}
.wo-field__value{font-size:6px;font-weight:700;margin-top:2px}
.menu-dot{position:absolute;right:0;top:5px;width:13px;height:13px;border-radius:50%;background:var(--brand-blue);display:flex;align-items:center;justify-content:center}
.menu-dot svg{width:6px;height:6px}
.wo-group .add-row{margin-top:5px;margin-bottom:0}
</style>
</head>
<body>

<svg width="0" height="0" style="position:absolute" aria-hidden="true">
  <symbol id="i-phone" viewBox="0 0 24 24"><path d="M6.6 10.8a15.1 15.1 0 0 0 6.6 6.6l2.2-2.2c.3-.3.7-.4 1-.2 1.1.4 2.3.6 3.6.6.6 0 1 .4 1 1V20c0 .6-.4 1-1 1C10.6 21 3 13.4 3 4c0-.6.4-1 1-1h3.5c.6 0 1 .4 1 1 0 1.3.2 2.5.6 3.6.1.3 0 .7-.2 1z"/></symbol>
  <symbol id="i-chat" viewBox="0 0 24 24"><path d="M3 4h12a2 2 0 0 1 2 2v6a2 2 0 0 1-2 2H8l-4 3v-3H3a2 2 0 0 1-2-2V6a2 2 0 0 1 2-2z"/><path d="M19 8h2a2 2 0 0 1 2 2v6a2 2 0 0 1-2 2h-1v3l-4-3h-5a2 2 0 0 1-2-2h6a3 3 0 0 0 3-3z"/></symbol>
  <symbol id="i-case" viewBox="0 0 24 24"><path d="M9 3h6a2 2 0 0 1 2 2v1h4a2 2 0 0 1 2 2v4H1V8a2 2 0 0 1 2-2h4V5a2 2 0 0 1 2-2zm0 2v1h6V5zM1 14h9v1h4v-1h9v5a2 2 0 0 1-2 2H3a2 2 0 0 1-2-2z"/></symbol>
  <symbol id="i-doc" viewBox="0 0 24 24"><path d="M5 2h14a1 1 0 0 1 1 1v18a1 1 0 0 1-1 1H5a1 1 0 0 1-1-1V3a1 1 0 0 1 1-1zm3 5v2h8V7zm0 4v2h8v-2zm0 4v2h5v-2z"/></symbol>
  <symbol id="i-grid" viewBox="0 0 24 24"><rect x="2" y="2" width="9" height="9" rx="2"/><rect x="13" y="2" width="9" height="9" rx="2"/><rect x="2" y="13" width="9" height="9" rx="2"/><rect x="13" y="13" width="9" height="9" rx="2"/></symbol>
  <symbol id="i-status" viewBox="0 0 22 7"><path d="M4 6.5 1 3.3a4.4 4.4 0 0 1 6 0z M0 2.2a6 6 0 0 1 8 0l-.6.6a5.2 5.2 0 0 0-6.8 0z" fill="#fff"/><rect x="12" y="1" width="9" height="5" rx="1" fill="none" stroke="#fff" stroke-width=".8"/><rect x="13.2" y="2.2" width="5.5" height="2.6" fill="#fff"/></symbol>
  <symbol id="i-back" viewBox="0 0 10 10"><path d="M6.5 1.5 3 5l3.5 3.5" fill="none" stroke="#fff" stroke-width="1.4" stroke-linecap="round" stroke-linejoin="round"/></symbol>
  <symbol id="i-search" viewBox="0 0 10 10"><circle cx="4.2" cy="4.2" r="3" fill="none" stroke="#fff" stroke-width="1.4"/><path d="m6.5 6.5 2.5 2.5" stroke="#fff" stroke-width="1.4" stroke-linecap="round"/></symbol>
  <symbol id="i-caret" viewBox="0 0 6 4"><path d="M0 0h6L3 4z" fill="#333"/></symbol>
  <symbol id="i-menu" viewBox="0 0 6 6"><path d="M0 1h6M0 3h6M0 5h6" stroke="#fff" stroke-width="1"/></symbol>
</svg>

<section class="screen screen--contact-edit">
  <header class="appbar">
    <div class="status"><span>9.41</span><svg><use href="#i-status"/></svg></div>
    <div class="back"><svg><use href="#i-back"/></svg></div>
    <h1 class="appbar__title">Contact</h1>
    <span class="btn-save">Save</span>
  </header>
  <main class="content">
    <div class="card form-card" style="top:12px">
      <p class="field-label">Business name</p><div class="field"></div>
      <p class="field-label">First name</p><div class="field"></div>
      <p class="field-label">Middle name</p><div class="field"></div>
      <p class="field-label">Last name</p><div class="field" style="margin-bottom:0"></div>
    </div>
    <div class="card form-card" style="top:184px;height:200px">
      <p class="field-label">Address Lable</p><div class="field"></div>
      <p class="field-label">Address Line 1</p><div class="field"></div>
      <p class="field-label">Address Line 2</p><div class="field"></div>
      <div class="row3">
        <div><p class="field-label">City</p><div class="field"></div></div>
        <div><p class="field-label">State</p><div class="field"></div></div>
        <div><p class="field-label">Zip</p><div class="field"></div></div>
      </div>
    </div>
  </main>
  <nav class="tabbar">
    <span class="tab tab--active"><svg><use href="#i-phone"/></svg></span>
    <span class="tab"><svg><use href="#i-chat"/></svg></span>
    <span class="tab"><svg><use href="#i-case"/></svg></span>
    <span class="tab"><svg><use href="#i-doc"/></svg></span>
    <span class="tab"><svg><use href="#i-grid"/></svg></span>
  </nav>
</section>

<section class="screen screen--pilots">
  <header class="appbar">
    <div class="status"><span>9.41</span><svg><use href="#i-status"/></svg></div>
    <div class="back"><svg><use href="#i-back"/></svg></div>
    <h1 class="appbar__title">Pilots</h1>
    <span class="action-plus">+</span>
  </header>
  <main class="content">
    <p class="search-label">Search</p>
    <div class="search"><span class="search__btn"><svg><use href="#i-search"/></svg></span></div>
    <div class="card pilot-list">
      <div class="pilot"><span class="avatar" style="background:#0a4fb0">A</span><div class="pilot__body"><p class="pilot__name">Abbott, Carl, Bryce, 3182133</p><span class="pilot__date">30 Sep 2024</span></div></div>
      <div class="pilot"><span class="avatar" style="background:#7cc242">B</span><div class="pilot__body"><p class="pilot__name">Bramley, Roger, 4467155</p><span class="pilot__date">28 Feb 2024</span></div></div>
      <div class="pilot"><span class="avatar" style="background:#3b3b3d">B</span><div class="pilot__body"><p class="pilot__name">Brandt, Owen, 2663187</p><span class="pilot__date">30 Oct 2024</span></div></div>
      <div class="pilot"><span class="avatar" style="background:#d55fe0">C</span><div class="pilot__body"><p class="pilot__name">Corsi, Elena, Mae, 4360575</p><span class="pilot__date">30 Mar 2024</span></div></div>
      <div class="pilot"><span class="avatar" style="background:#0a4fb0">C</span><div class="pilot__body"><p class="pilot__name">Castro Lopez, Mateo, Ivan</p><span class="pilot__date">30 Sep 2024</span></div></div>
      <div class="pilot"><span class="avatar" style="background:#12a84a">G</span><div class="pilot__body"><p class="pilot__name">Gilmore, Dean, 3423819</p><span class="pilot__date">28 Feb 2025</span></div></div>
      <div class="pilot"><span class="avatar" style="background:#f39a1e">G</span><div class="pilot__body"><p class="pilot__name">Grant, Peter, Lee, 2761635</p><span class="pilot__date">06 Mar 2023</span></div></div>
    </div>
  </main>
  <nav class="tabbar">
    <span class="tab tab--active"><svg><use href="#i-phone"/></svg></span>
    <span class="tab"><svg><use href="#i-chat"/></svg></span>
    <span class="tab"><svg><use href="#i-case"/></svg></span>
    <span class="tab"><svg><use href="#i-doc"/></svg></span>
    <span class="tab"><svg><use href="#i-grid"/></svg></span>
  </nav>
</section>

<section class="screen screen--contact-read">
  <header class="appbar">
    <div class="status"><span>9.41</span><svg><use href="#i-status"/></svg></div>
    <div class="back"><svg><use href="#i-back"/></svg></div>
    <h1 class="appbar__title">Contact</h1>
    <span class="action-plus">+</span>
  </header>
  <main class="content">
    <div class="card add-group">
      <div class="add-row"><span class="plus-dot">+</span>Add Email -e</div>
      <div class="add-row"><span class="plus-dot">+</span>Add Social Media -e</div>
      <div class="add-row"><span class="plus-dot">+</span>Add Emergency Contact -e</div>
      <div class="add-row"><span class="plus-dot">+</span>Add Personal Information -e</div>
      <div class="add-row"><span class="plus-dot">+</span>Add Work Info -e</div>
      <div class="add-row"><span class="plus-dot">+</span>Add Skills/Talents -e</div>
      <div class="add-row" style="margin-bottom:0"><span class="plus-dot">+</span>Add Resources -e</div>
    </div>
    <div class="card linked-group">
      <div class="linked linked--teal">
        <div class="linked__head"><b>Pilots-e</b><span>Collapse</span></div>
        <div class="select">Ashford, Cole, 3647946, 10/31/23<span class="select__caret"><svg><use href="#i-caret"/></svg></span></div>
      </div>
      <div class="linked linked--blue">
        <div class="linked__head"><b>Aircraft Owner-e</b><span>Collapse</span></div>
        <div class="select">Personal: Ashford, Cole: Veloran: V12:<br>Veloran AirWorks, Single Engine,<br>1100<span class="select__caret"><svg><use href="#i-caret"/></svg></span></div>
      </div>
    </div>
  </main>
  <nav class="tabbar">
    <span class="tab tab--active"><svg><use href="#i-phone"/></svg></span>
    <span class="tab"><svg><use href="#i-chat"/></svg></span>
    <span class="tab"><svg><use href="#i-case"/></svg></span>
    <span class="tab"><svg><use href="#i-doc"/></svg></span>
    <span class="tab"><svg><use href="#i-grid"/></svg></span>
  </nav>
</section>

<section class="screen screen--work-order">
  <header class="appbar">
    <div class="status"><span>9.41</span><svg><use href="#i-status"/></svg></div>
    <div class="back"><svg><use href="#i-back"/></svg></div>
    <h1 class="appbar__title">Work Order</h1>
    <span class="action-plus">+</span>
  </header>
  <main class="content">
    <div class="chips">
      <span class="chip">Extra Soft</span><span class="chip">Soft</span><span class="chip chip--active">Medium</span><span class="chip">Hard</span>
    </div>
    <div class="chip-tools">
      <svg viewBox="0 0 10 10"><path d="M2 0h6v3H2zM0 3.5h10V8H8v2H2V8H0zM3 6.5v2.5h4V6.5z"/></svg>
      <svg viewBox="0 0 10 10"><path d="M1 1h8v8H1zm2 2v4h4V3z"/></svg>
    </div>
    <div class="card wo-group">
      <div class="wo-detail">
        <div class="wo-field"><p class="wo-field__label">Customer - e</p><p class="wo-field__value">Amari, Nadia</p><span class="menu-dot"><svg><use href="#i-menu"/></svg></span></div>
        <div class="wo-field"><p class="wo-field__label">Service Location - e</p><p class="wo-field__value">Billing, 1820 Harbor Ridge Way, Millbrook</p></div>
        <div class="wo-field"><p class="wo-field__label">Billing Address - e</p><p class="wo-field__value">Billing, 1820 Harbor Ridge Way, Millbrook</p></div>
        <div class="wo-field"><p class="wo-field__label">Description - e</p><p class="wo-field__value">Pool maintenance</p></div>
        <div class="wo-field"><p class="wo-field__label">Work Order Type - e</p><p class="wo-field__value">One off job - e</p></div>
        <div class="wo-field"><p class="wo-field__label">WO Status - e</p><p class="wo-field__value">Active - e</p></div>
        <div class="wo-field"><p class="wo-field__label">Billing Frequency - e</p><p class="wo-field__value">Upon job completion</p></div>
      </div>
      <div class="add-row"><span class="plus-dot">+</span>Add Technician - e</div>
      <div class="add-row"><span class="plus-dot">+</span>Add Line Items - e</div>
    </div>
  </main>
  <nav class="tabbar">
    <span class="tab"><svg><use href="#i-phone"/></svg></span>
    <span class="tab"><svg><use href="#i-chat"/></svg></span>
    <span class="tab tab--active"><svg><use href="#i-case"/></svg></span>
    <span class="tab"><svg><use href="#i-doc"/></svg></span>
    <span class="tab"><svg><use href="#i-grid"/></svg></span>
  </nav>
</section>

</body>
</html>
```